Need Business Card for our Real Estate Business with Sales Executive's Picture

PANTONE 484 C ( RED)

PANTONE 2766 C ( BLUE

Industry/Entity Type

Real Estate

Contact Information for Business Card

Name, Mobile, email, & picture of Person
Agency Phone, address, Web address

Requirements
Must have
• Our Logo Colours, Agent Picture,

```html
<!DOCTYPE html>
<html lang="en">
<head>
<meta charset="utf-8">
<title>Mesa Ridge Realty — Business Card</title>
<link rel="stylesheet" href="https://fonts.googleapis.com/css2?family=Ubuntu:wght@400;500&display=swap">
<style>
  :root {
    --page: #e9e7e4;
    --card: #f7f6f3;
    --navy: #1f2d5c;
    --navy-deep: #16224a;
    --red: #a8282b;
    --white: #ffffff;
    --soft-text: #c9cee2;
  }
  html, body {
    margin: 0;
    width: 1200px;
    height: 1054px;
    overflow: hidden;
    background: var(--page);
    font-family: "Ubuntu", Arial, sans-serif;
  }
  .card {
    position: absolute;
    left: 100px;
    top: 225px;
    width: 1000px;
    height: 604px;
    background: var(--card);
    overflow: hidden;
    box-shadow: 0 10px 30px rgba(0,0,0,0.18);
  }
  .card-art { position: absolute; inset: 0; }
  .edge-dot {
    position: absolute;
    left: -28px;
    top: 82px;
    width: 56px;
    height: 56px;
    border-radius: 50%;
    background: var(--red);
  }
  .person-name {
    position: absolute;
    left: 51px;
    top: 78px;
    margin: 0;
    font-size: 34px;
    font-weight: 500;
    color: var(--navy);
  }
  .person-role {
    position: absolute;
    left: 51px;
    top: 121px;
    margin: 0;
    font-size: 25px;
    font-weight: 400;
    color: var(--red);
  }
  .brand {
    position: absolute;
    left: 430px;
    top: 80px;
    display: flex;
    align-items: center;
    gap: 18px;
  }
  .brand-mark {
    width: 26px;
    height: 26px;
    background: var(--navy);
  }
  .brand-name {
    font-size: 46px;
    font-weight: 400;
    letter-spacing: 4px;
    color: var(--navy);
    text-transform: uppercase;
  }
  .contact-list {
    position: absolute;
    left: 60px;
    top: 398px;
    margin: 0;
    padding: 0;
    list-style: none;
  }
  .contact-list li {
    display: flex;
    align-items: center;
    height: 33px;
    font-size: 24px;
    color: var(--white);
  }
  .contact-list svg {
    width: 20px;
    height: 20px;
    margin-right: 16px;
    flex: none;
  }
  .office-address {
    position: absolute;
    left: 51px;
    top: 538px;
    margin: 0;
    font-size: 24px;
    color: var(--soft-text);
  }
  .agent-photo {
    position: absolute;
    left: 620px;
    top: 210px;
    width: 380px;
    height: 394px;
    background: linear-gradient(180deg, rgba(190,160,140,0.35) 0%, rgba(176,140,118,0.85) 35%, rgba(40,56,110,0.95) 70%, var(--navy-deep) 100%);
    -webkit-mask-image: linear-gradient(90deg, transparent 0%, #000 18%);
    mask-image: linear-gradient(90deg, transparent 0%, #000 18%);
  }
</style>
</head>
<body>
  <div class="card">
    <svg class="card-art" viewBox="0 0 1000 604" width="1000" height="604" aria-hidden="true">
      <path d="M0,232 C220,220 420,280 600,370 C700,420 790,440 860,420 L1000,362 L1000,384 L860,442 C780,464 690,442 590,394 C410,307 210,252 0,254 Z" fill="var(--red)"/>
      <path d="M0,300 C220,290 420,350 600,440 C700,486 790,500 870,472 L1000,420 L1000,604 L0,604 Z" fill="var(--navy)"/>
    </svg>

    <span class="edge-dot"></span>

    <h1 class="person-name">Maren Holloway</h1>
    <p class="person-role">Managing Director</p>

    <div class="brand">
      <span class="brand-mark"></span>
      <span class="brand-name">Mesa Ridge Realty</span>
    </div>

    <ul class="contact-list">
      <li>
        <svg viewBox="0 0 20 20"><rect x="5" y="1" width="10" height="18" rx="2" fill="none" stroke="#fff" stroke-width="2"/><circle cx="10" cy="15.5" r="1.2" fill="#fff"/></svg>
        555.210.4837
      </li>
      <li>
        <svg viewBox="0 0 20 20"><path d="M2,7 C2,3 18,3 18,7 L15,9 L13,7 L7,7 L5,9 Z" fill="#fff"/><rect x="4" y="10" width="12" height="8" rx="1" fill="#fff"/></svg>
        555-318-6642
      </li>
      <li>
        <svg viewBox="0 0 20 20"><rect x="1" y="4" width="18" height="12" fill="none" stroke="#fff" stroke-width="2"/><path d="M1,4 L10,11 L19,4" fill="none" stroke="#fff" stroke-width="2"/></svg>
        mesaridgehomes.com
      </li>
      <li>
        <svg viewBox="0 0 20 20"><circle cx="10" cy="10" r="8" fill="none" stroke="#fff" stroke-width="1.8"/><ellipse cx="10" cy="10" rx="3.5" ry="8" fill="none" stroke="#fff" stroke-width="1.5"/><path d="M2,10 H18" stroke="#fff" stroke-width="1.5"/></svg>
        mholloway@mesaridgehomes.com
      </li>
    </ul>

    <p class="office-address">418 Aspen Court #210, Fairview, CO 80231</p>

    <div class="agent-photo" role="img" aria-label="Portrait photo of the sales agent in a navy suit and tie"></div>
  </div>
</body>
</html>
```